Counseling Practice Business Card

I need a professional looking business card incorporating my new logo that was just completed. Card needs to incorporate my name and title, description of my specialty, my address, my phone number, my fax number, my email and my website URL. I need to be able to choose design on/with different paper colors and textures.
I do not have a lot of business card ideas so I am open to anything but I want bold,sharp, clear card without additional designs other than my logo (see attached file info). I am open to different color backgrounds or paper colors including black. I do not like traditional brackets around area codes in phone number or dashes between numbers in phone number. Am open to other ways of presenting including periods between numbers as appropriate. I do not know enough to know what I like yet but I want card to coordinate and work together with my logo. My practice emphasizes natural mental health interventions so any use of color (with background paper color or the blue and green in my logo) that elicits nature is nice. In addition to black, any natural brown or wood looking background might be desirable also. Most of the offerings so far look very similar and boring.

Target Market(s)

Potential therapy clients and other professionals

Contact Information for Business Card

Card information:
Gerald M. Whitcombe, Ph.D.
Licensed Clinical Psychologist
Integrative Health Coach
4812 Marlowe Ridge Blvd SE
Suite 310
Duluth, GA 30096
(770) 415-2983 phone
(770) 581-4096 fax
drgeraldwhitcombe@quillmarsh.net
brightfernwellness.net

Font styles to use
Serif
Sans Serif
Other font styles liked:
• anything that you think looks crisp, clear and easily readable

Requirements
Must have
• Any color used should coordinate with my logo design (see attached files).
• Card should be printed horizontally so top and bottom are longest sides of rectangle.
• Background color or paper color should complement and highlight logo. Do not like a white background. black, grey, brown or any color my logo would blend well with.
Nice to have
• I would like designer to utilize color to highlight letters/name or phone-fax-web symbols.
• Bottom edge of card could be highlighted if appropriate to an idea.
Should not have
• I would NOT want the card to have a pure white background at all.
• No clear cards.
• Cards should be oriented with long sides on bottom and top, NOT sides. DO NOT LIKE THIS THIN TALL ORIENTATION.

```html
<!DOCTYPE html>
<html lang="en">
<head>
<meta charset="utf-8">
<title>Brightfern Wellness – Business Card</title>
<link rel="stylesheet" href="https://fonts.googleapis.com/css2?family=Open+Sans:wght@400;600;700&display=swap">
<style>
  :root {
    --backdrop: #3a3a3c;
    --kraft: #cfb084;
    --kraft-deep: #bd9c6f;
    --kraft-ink: #b29066;
    --forest: #1c5a2c;
    --teal: #1f5d73;
    --ink: #1d1b18;
    --url-ink: #d9e6ea;
  }
  * { margin: 0; padding: 0; box-sizing: border-box; }
  html, body { width: 799px; height: 1200px; overflow: hidden; }
  body {
    background: var(--backdrop);
    font-family: "Open Sans", Arial, sans-serif;
    position: relative;
  }
  .card {
    position: absolute;
    left: 80px;
    width: 640px;
    height: 366px;
    background: radial-gradient(ellipse at 40% 30%, var(--kraft) 0%, var(--kraft-deep) 100%);
    overflow: hidden;
  }
  .card--front { top: 150px; }
  .card--back { top: 690px; }

  .front-wordmark {
    position: absolute;
    left: 0; right: 0; top: 150px;
    text-align: center;
    font-size: 48px;
    font-weight: 600;
    color: var(--kraft-ink);
    letter-spacing: 1px;
  }

  .back-wordmark {
    position: absolute;
    left: 36px; top: 120px;
    display: flex; align-items: center; gap: 10px;
    font-size: 27px;
    font-weight: 700;
    color: var(--teal);
  }
  .back-wordmark .dot {
    width: 14px; height: 14px; border-radius: 50%;
    background: var(--forest);
  }

  .contact {
    position: absolute;
    left: 350px; top: 62px;
    color: var(--ink);
    font-size: 13px;
    line-height: 1.35;
  }
  .contact .name {
    font-size: 17px;
    font-weight: 700;
    color: var(--teal);
    margin-bottom: 4px;
  }
  .contact .title { margin-bottom: 12px; }
  .contact .address { margin-bottom: 8px; }
  .contact .line { display: flex; align-items: center; gap: 7px; }
  .contact .line svg { width: 12px; height: 12px; fill: var(--teal); flex: none; }

  .band-green {
    position: absolute;
    left: 0; bottom: 0;
    width: 330px; height: 22px;
    background: var(--forest);
  }
  .band-teal {
    position: absolute;
    left: 300px; right: 0; bottom: 0;
    height: 58px;
    background: var(--teal);
    border-top-left-radius: 22px;
    display: flex; align-items: center;
    padding-left: 48px;
    color: var(--url-ink);
    font-size: 15px;
  }
</style>
</head>
<body>
  <section class="card card--front" aria-label="Card front">
    <div class="front-wordmark">Brightfern Wellness</div>
  </section>

  <section class="card card--back" aria-label="Card back">
    <div class="back-wordmark"><span class="dot"></span>Brightfern Wellness</div>

    <div class="contact">
      <div class="name">Gerald M. Whitcombe, Ph.D.</div>
      <div class="title">Licensed Clinical Psychologist<br>Integrative Health Coach</div>
      <div class="address">4812 Marlowe Ridge Blvd SE<br>Suite 310 Duluth, GA 30096</div>
      <div class="line">
        <svg viewBox="0 0 24 24" aria-hidden="true"><path d="M6.6 10.8a15.1 15.1 0 0 0 6.6 6.6l2.2-2.2a1 1 0 0 1 1-.25 11.4 11.4 0 0 0 3.6.57 1 1 0 0 1 1 1V20a1 1 0 0 1-1 1A17 17 0 0 1 3 4a1 1 0 0 1 1-1h3.5a1 1 0 0 1 1 1c0 1.25.2 2.45.57 3.57a1 1 0 0 1-.25 1z"/></svg>
        770.415.2983
      </div>
      <div class="line">
        <svg viewBox="0 0 24 24" aria-hidden="true"><path d="M7 3h10v5H7zM4 9h16a2 2 0 0 1 2 2v6h-4v4H6v-4H2v-6a2 2 0 0 1 2-2zm4 7v3h8v-3z"/></svg>
        770.581.4096
      </div>
      <div class="line">
        <svg viewBox="0 0 24 24" aria-hidden="true"><path d="M2 5h20v14H2zm2 2v.5l8 5 8-5V7z"/></svg>
        drgeraldwhitcombe@quillmarsh.net
      </div>
    </div>

    <div class="band-green"></div>
    <div class="band-teal">www.brightfernwellness.net</div>
  </section>
</body>
</html>
```